KV HOLDING Business Cards

I need business cards for "KV Holding group LLC" doublesided... logo on the back (also include logo on front)
logo attached to project... i have jpg up..
Company Info:
827 North Cadwell Avenue, Suite 4B
Chicago, Illinois 60654
facsimile 312-481-2075 (list fax, address, website on all cards.)
www.kvholdinggroup.example
Three different people on cards:
Darnell P. Okafor, CPA MST
Principal
ofc 312-481-3900
mobile 312-204-7751
darnellpokafor@kvholdinggroup.example
Hollis T. Brennecke, CPA MST
Principal
hollistbrennecke@kvholdinggroup.example
mobile 708-539-1184
ofc 312-481-3900
Conrad M Pavlik
Principal
ofc 312-481-3900
no mobile
conradmpavlik@kvholdinggroup.example
I have multiple projects listed.. see below:
Business cards for amber gate ventures llc
letterhead
envelopes
Business cards for KV Holding LLC
letterhead
envelopes
Target Market(s)
rich people
Industry/Entity Type
Business
Look and feel
Each slider illustrates characteristics of the customer's brand and the style your logo design should communicate.

```html
<!DOCTYPE html>
<html lang="en">
<head>
<meta charset="utf-8">
<title>KV Holding Group LLC — Business Cards</title>
<link rel="stylesheet" href="https://fonts.googleapis.com/css2?family=Roboto:wght@400;500&display=swap">
<style>
  :root {
    --backdrop: #3a3a3c;
    --navy: #163e6f;
    --card-grey: #c4c4c6;
    --card-white: #ffffff;
    --band-text: #ffffff;
  }
  * { margin: 0; padding: 0; box-sizing: border-box; }
  html, body { width: 1200px; height: 1000px; overflow: hidden; }
  body {
    background: var(--backdrop);
    font-family: "Roboto", Arial, sans-serif;
    color: var(--navy);
    position: relative;
  }
  .card {
    position: absolute;
    width: 500px;
    height: 293px;
    overflow: hidden;
    box-shadow: 0 14px 18px -10px rgba(0,0,0,0.7);
  }
  .card--back { left: 76px; background: var(--card-grey); }
  .card--front { left: 631px; background: var(--card-white); }
  .row-1 { top: 30px; }
  .row-2 { top: 348px; }
  .row-3 { top: 667px; }

  .band {
    position: absolute;
    left: 0; right: 0; bottom: 0;
    height: 46px;
    background: var(--navy);
    color: var(--band-text);
    display: flex;
    align-items: center;
  }
  .card--back .band {
    justify-content: center;
    font-size: 21px;
    letter-spacing: 3px;
  }
  .card--front .band {
    padding-left: 35px;
    font-size: 10.5px;
  }

  .brand-mark {
    position: absolute;
    border-radius: 50%;
    background: var(--navy);
  }
  .brand-name {
    position: absolute;
    font-weight: 400;
    color: var(--navy);
    white-space: nowrap;
    text-align: center;
  }
  .card--back .brand-mark { width: 96px; height: 96px; left: 202px; top: 62px; }
  .card--back .brand-name { left: 0; right: 0; top: 178px; font-size: 34px; }

  .card--front .brand-mark { width: 44px; height: 44px; left: 362px; top: 56px; }
  .card--front .brand-name { left: 296px; width: 180px; top: 112px; font-size: 15px; }

  .person {
    position: absolute;
    left: 35px;
    top: 76px;
  }
  .person__name { font-size: 22px; line-height: 24px; font-weight: 400; }
  .person__title { font-size: 13px; line-height: 14px; }
  .rule {
    position: absolute;
    left: 0;
    width: 283px;
    top: 117px;
    height: 3px;
    background: var(--navy);
  }
  .contacts {
    position: absolute;
    left: 35px;
    top: 149px;
    list-style: none;
    font-size: 11px;
    line-height: 14.5px;
  }
  .row-2 .contacts { top: 166px; line-height: 17px; }
  .row-3 .contacts { top: 160px; line-height: 17px; }
</style>
</head>
<body>

  <!-- Back cards -->
  <section class="card card--back row-1">
    <span class="brand-mark"></span>
    <span class="brand-name">KV Holding Group LLC</span>
    <div class="band">www.kvholdinggroup.example</div>
  </section>
  <section class="card card--back row-2">
    <span class="brand-mark"></span>
    <span class="brand-name">KV Holding Group LLC</span>
    <div class="band">www.kvholdinggroup.example</div>
  </section>
  <section class="card card--back row-3">
    <span class="brand-mark"></span>
    <span class="brand-name">KV Holding Group LLC</span>
    <div class="band">www.kvholdinggroup.example</div>
  </section>

  <!-- Front cards -->
  <section class="card card--front row-1">
    <div class="person">
      <h2 class="person__name">Darnell P. Okafor, CPA MST</h2>
      <p class="person__title">Principal</p>
    </div>
    <span class="rule"></span>
    <span class="brand-mark"></span>
    <span class="brand-name">KV Holding Group LLC</span>
    <ul class="contacts">
      <li>Office : 312-481-3900</li>
      <li>Direct : 312-481-6218</li>
      <li>Mobile : 312-204-7751</li>
      <li>Facsimile : 312-481-2075</li>
      <li>Email : darnellpokafor@kvholdinggroup.example</li>
    </ul>
    <div class="band">827 North Cadwell Avenue, Suite 4B Chicago, Illinois 60654 &nbsp;|&nbsp; www.kvholdinggroup.example</div>
  </section>

  <section class="card card--front row-2">
    <div class="person">
      <h2 class="person__name">Hollis T. Brennecke, CPA MST</h2>
      <p class="person__title">Principal</p>
    </div>
    <span class="rule"></span>
    <span class="brand-mark"></span>
    <span class="brand-name">KV Holding Group LLC</span>
    <ul class="contacts">
      <li>Office : 312-481-3900</li>
      <li>Mobile : 708-539-1184</li>
      <li>Facsimile : 312-481-2075</li>
      <li>Email : hollistbrennecke@kvholdinggroup.example</li>
    </ul>
    <div class="band">827 North Cadwell Avenue, Suite 4B Chicago, Illinois 60654 &nbsp;|&nbsp; www.kvholdinggroup.example</div>
  </section>

  <section class="card card--front row-3">
    <div class="person">
      <h2 class="person__name">Conrad M Pavlik</h2>
      <p class="person__title">Principal</p>
    </div>
    <span class="rule"></span>
    <span class="brand-mark"></span>
    <span class="brand-name">KV Holding Group LLC</span>
    <ul class="contacts">
      <li>Office : 312-481-3900</li>
      <li>Facsimile : 312-481-2075</li>
      <li>Email : conradmpavlik@kvholdinggroup.example</li>
    </ul>
    <div class="band">827 North Cadwell Avenue, Suite 4B Chicago, Illinois 60654 &nbsp;|&nbsp; www.kvholdinggroup.example</div>
  </section>

</body>
</html>
```